Verdant Drop Tincture

I need a supplement label for my new CBD Tincture.
Please include images relative to both the Nervous and Cannabinoid System.
Looking for scientific appeal.

Target Market(s)

Alternative Medicine Clinics

Industry/Entity Type

Holistic Supplements

Colors
59FF00
82FF00
B8FF75
E3FFCB
F4FFEA
FFC000
F8CF3A
FAE287
FDF2CF
FEFAEE

Requirements
Must have
• "New Clinical Strength"

```html
<!DOCTYPE html>
<html lang="en">
<head>
<meta charset="UTF-8">
<title>Verdant Drop Tincture Label</title>
<link href="https://fonts.googleapis.com/css2?family=Poppins:wght@700;800&family=Roboto:wght@400;500;700&family=Barlow+Condensed:wght@500;600&family=Barlow:wght@500;600&display=swap" rel="stylesheet">
<style>
  :root{
    --lime:#59ff00;
    --lime-2:#82ff00;
    --lime-soft:#b8ff75;
    --lime-pale:#e3ffcb;
    --lime-mist:#f4ffea;
    --gold:#ffc000;
    --gold-2:#f8cf3a;
    --gold-soft:#fae287;
    --cream:#fefaee;
    --leaf:#2f8a00;
    --ink:#1d1d1d;
    --panel:#ffffff;
    --tab:#fdf2cf;
    --base:#6b6b6b;
    --page:#ffffff;
  }
  *{box-sizing:border-box;margin:0;padding:0}
  html,body{width:954px;height:1200px;overflow:hidden;background:var(--page)}
  body{position:relative;font-family:"Roboto",sans-serif;color:var(--ink)}

  .label{position:absolute;left:17px;top:435px;width:920px;height:330px;background:var(--cream);overflow:hidden}
  .label__band{position:absolute;left:0;top:0;width:100%;height:127px;background:linear-gradient(90deg,var(--lime) 0%,var(--lime-2) 55%,var(--gold-2) 100%)}
  .label__base{position:absolute;left:0;bottom:0;width:100%;height:8px;background:var(--base)}
  .label__tab{position:absolute;left:385px;bottom:8px;width:150px;height:36px;background:var(--tab);clip-path:polygon(12% 0,88% 0,100% 100%,0 100%);text-align:center;padding-top:5px;font-size:10.5px;line-height:13px}
  .label__tab u{text-decoration:underline}

  .panel{position:absolute;top:23px;width:221px;height:281px;background:var(--panel);border:1px solid var(--lime-soft);border-radius:9px}
  .panel--use{left:34px;padding:12px 11px 0}
  .panel--facts{left:664px;padding:15px 0 0}

  .use-text{font-size:9.4px;line-height:12.3px;margin-bottom:9px;hyphens:auto}
  .use-text b{font-weight:700}
  .warning{background:var(--gold);color:var(--ink);font-family:"Barlow Condensed",sans-serif;font-weight:600;font-size:10.5px;padding:3px 6px;margin-bottom:6px;letter-spacing:.2px}
  .badges{display:flex;gap:5px;align-items:center;margin-bottom:6px}
  .badge{width:33px;height:33px;border-radius:50%}
  .badge--reg{background:var(--leaf)}
  .badge--lab{background:var(--gold)}
  .badge--gmp{background:var(--lime-2)}
  .badge--origin{background:var(--gold-2)}
  .badge--cycle{background:var(--lime)}
  .disclaimer{border:1px solid #444;font-size:7px;line-height:9.5px;text-align:center;padding:4px 5px;margin-bottom:7px}
  .lot{font-size:8px;line-height:10.5px;text-align:center;font-weight:500}

  .hero{position:absolute;left:320px;top:6px;width:280px;text-align:center}
  .hero__brand{font-family:"Barlow",sans-serif;font-weight:600;font-size:12px;letter-spacing:3px;line-height:14px;color:var(--ink)}
  .hero__name{font-family:"Poppins",sans-serif;font-weight:800;font-size:90px;line-height:84px;color:var(--ink);letter-spacing:-1px}
  .hero__spectrum{display:inline-block;margin-top:2px;width:209px;height:29px;background:var(--ink);color:#fff;border-radius:3px;font-family:"Barlow",sans-serif;font-weight:600;font-size:22px;line-height:29px}
  .hero__molecule{display:block;margin:7px auto 0;width:170px;height:70px;background:linear-gradient(180deg,var(--lime-mist),var(--lime-pale));border-radius:4px}
  .hero__tags{display:flex;justify-content:center;gap:5px;margin-top:5px}
  .hero__size,.hero__clinical{font-family:"Barlow Condensed",sans-serif;font-weight:600;font-size:11px;line-height:14px;padding:0 9px;border-radius:8px}
  .hero__size{background:var(--leaf);color:#fff}
  .hero__clinical{background:var(--gold);color:var(--ink)}
  .hero__dose{font-family:"Poppins",sans-serif;font-weight:800;font-size:23px;line-height:26px;color:var(--leaf)}

  .facts{margin:0 14px;border:1px solid #333;padding:0 0 5px}
  .facts__title{background:var(--leaf);color:#fff;font-weight:700;font-size:16.5px;text-align:center;line-height:20px;margin:0 0 4px}
  .facts__serving{font-size:6.8px;line-height:9px;padding:0 7px 4px;border-bottom:1.5px solid #333;margin:0 7px}
  .facts__row{display:grid;grid-template-columns:1fr 44px 26px;font-size:6.8px;padding:4px 0;margin:0 7px;border-bottom:1px solid #333;white-space:nowrap}
  .facts__row span:last-child{text-align:right}
  .facts__row--head{font-weight:700;border-bottom:1px solid #999}
  .facts__note{font-size:6.8px;font-weight:700;padding:4px 7px 0}
  .ingredients{text-align:center;padding:10px 8px 7px;border-bottom:1px solid var(--lime-soft)}
  .ingredients__title{color:var(--leaf);font-weight:700;font-size:12px;line-height:15px}
  .ingredients__list{font-weight:700;font-size:11.5px;line-height:15px}
  .thc{color:var(--leaf);font-weight:700;font-size:12px;text-align:center;padding:7px 0;border-bottom:1px solid var(--lime-soft)}
  .distributor{font-size:7.6px;font-weight:700;text-align:center;line-height:10.2px;padding-top:7px}
</style>
</head>
<body>
  <div class="label">
    <div class="label__band"></div>

    <section class="panel panel--use">
      <p class="use-text"><b>SUGGESTED USE:</b> Shake well. Take 1-2 servings daily or as needed. Hold under tongue for 60 seconds and swallow.</p>
      <p class="use-text"><b>CAUTION:</b> Consult your healthcare provider if you're nursing, pregnant, or taking medication. If adverse reactions occur, discontinue use and consult your physician.</p>
      <div class="warning">KEEP OUT OF THE REACH OF CHILDREN.</div>
      <div class="badges">
        <span class="badge badge--reg"></span>
        <span class="badge badge--lab"></span>
        <span class="badge badge--gmp"></span>
        <span class="badge badge--origin"></span>
        <span class="badge badge--cycle"></span>
      </div>
      <p class="disclaimer">*These statement have not been evaluated by the Food and Drug Administration. This product is not intended to diagnose, treat, cure, or prevent any disease.</p>
      <p class="lot">Lot # and Expiration Date Printed<br>on Bottom of Bottle.<br>SKU:ROC913</p>
    </section>

    <section class="hero">
      <p class="hero__brand">VERDANT DROP</p>
      <h1 class="hero__name">CBD</h1>
      <div class="hero__spectrum">FULL SPECTRUM</div>
      <span class="hero__molecule" role="img" aria-label="Line drawing of the cannabidiol molecular structure"></span>
      <div class="hero__tags">
        <span class="hero__size">1 OZ. TINTURE</span>
        <span class="hero__clinical">NEW CLINICAL STRENGTH</span>
      </div>
      <div class="hero__dose">2000MG</div>
    </section>

    <div class="label__tab"><u>FULL SPECTRUM</u><br>1 oz (30ML)</div>

    <section class="panel panel--facts">
      <div class="facts">
        <h2 class="facts__title">SUPPLEMENT FACTS</h2>
        <p class="facts__serving">Serving Size: 1 ML (1 Dropper) 66.66mg Full<br>Spectrum (CBD) Extract.<br>Servings Per Container: 30</p>
        <div class="facts__row facts__row--head"><span>Amount Per Serving</span><span>% Daily</span><span>Value</span></div>
        <div class="facts__row"><span>Full Spectrum (CBD) Extract</span><span>66.66mg</span><span>*</span></div>
        <p class="facts__note">* Daily Value not established.</p>
      </div>
      <div class="ingredients">
        <p class="ingredients__title">INGREDIENTS:</p>
        <p class="ingredients__list">MCT OIL, FULL SPECTRUM (CBD)<br>EXTRACT, TERPENES.</p>
      </div>
      <p class="thc">Total Potential THC** &nbsp;1.245mg/g</p>
      <p class="distributor">Distributed By: Verdant Drop<br>Street Address City, ST Zipcode<br>Website or Phone Number</p>
    </section>

    <div class="label__base"></div>
  </div>
</body>
</html>
```